New Business Card Design for Manufacturing

We are an engineering/manufacturing company that offers Advanced machining/assembly/engineering services, as well as innovative products for the heavy duty engine cooling markets.

We are looking to get a new business card designed that is clean and modern looking, but still fits the wide range of technical/skilled work we do.

- We hope to use this design as the base for other design work in new Presentations, web, and print work.

Industry/Entity Type

Engineering

Contact Information for Business Card

Our preferred color of blue is (RGB) 22/71/159 but can vary slightly from that color. Our content will be our Logo and full company name (Vantrell Forge Works, Inc.), company address, name, job title, phone number with extension, cell number, fax number, website, and email address on the cards.
We'd like the full company name next to the logo, but we are open to other interpretations of that layout.
Preferably, we would like the back side to be clean with just our logo, and the front to contain all of the contact information.

Colors
2f74b4
0355a3
85abd2

Requirements
Must have
• - Logo, company name, needed content - We are open to interpretation beyond that.
• - Standard size business card.
• - Horizontal orientation.
• - Enough space for lengthy names / job titles (for example, a job title could read "Directory of Human Resources" or "V.P. of Governmental Affairs"). We need this to look clean, whether the title be short (CEO) or long (as described above).

```html
<!DOCTYPE html>
<html lang="en">
<head>
<meta charset="utf-8">
<title>Vantrell Forge Works – Business Card</title>
<link rel="stylesheet" href="https://fonts.googleapis.com/css2?family=Fira+Sans:wght@400;500;800&family=Open+Sans:wght@400;600&display=swap">
<style>
  :root {
    --brand-blue: #03559e;
    --brand-blue-deep: #004b8f;
    --steel-grey: #7d8791;
    --paper: #f7f7f7;
    --paper-shade: #e4e4e4;
    --ink: #3a3a3a;
    --stage: #e8e8e8;
    --white: #ffffff;
  }
  * { margin: 0; padding: 0; box-sizing: border-box; }
  html, body { width: 1200px; height: 576px; overflow: hidden; background: var(--stage); }
  .canvas { position: relative; width: 1200px; height: 576px; }

  .card {
    position: absolute; top: 138px; height: 294px; border-radius: 13px; overflow: hidden;
  }

  /* Back side */
  .card--back {
    left: 82px; width: 485px;
    background: linear-gradient(180deg, var(--brand-blue) 0%, var(--brand-blue-deep) 100%);
    color: var(--white); text-align: center;
  }
  .card--back .wordmark {
    position: absolute; left: 0; right: 0; top: 104px;
    font-family: "Fira Sans", sans-serif; font-weight: 800; font-size: 40px; line-height: 48px;
  }
  .card--back .tagline {
    position: absolute; left: 0; right: 0; top: 172px;
    font-family: "Fira Sans", sans-serif; font-weight: 800; font-size: 17px; letter-spacing: 1px;
  }
  .card--back .site {
    position: absolute; left: 0; right: 0; top: 265px;
    display: flex; align-items: center; justify-content: center; gap: 14px;
    font-family: "Open Sans", sans-serif; font-size: 13px;
  }
  .site .rule { width: 52px; height: 2px; background: linear-gradient(90deg, transparent, var(--white), transparent); }

  /* Front side */
  .card--front {
    left: 602px; width: 481px;
    background: linear-gradient(180deg, var(--white) 0%, var(--paper) 55%, var(--paper-shade) 100%);
    font-family: "Open Sans", sans-serif; color: var(--ink);
  }
  .header-band {
    position: absolute; left: 0; top: 0; width: 100%; height: 76px;
    background: var(--brand-blue);
    border-bottom: 5px solid var(--steel-grey);
  }
  .holder { position: absolute; right: 21px; top: 20px; text-align: right; color: var(--white); }
  .holder .name { font-family: "Fira Sans", sans-serif; font-weight: 500; font-size: 21px; line-height: 1.1; }
  .holder .role { font-family: "Open Sans", sans-serif; font-size: 11.5px; margin-top: 4px; }

  .card--front .wordmark {
    position: absolute; left: 24px; top: 100px;
    font-family: "Fira Sans", sans-serif; font-weight: 800; font-size: 30px; line-height: 36px; color: var(--brand-blue);
  }
  .card--front .tagline {
    position: absolute; left: 25px; top: 144px;
    font-family: "Fira Sans", sans-serif; font-weight: 800; font-size: 13px; letter-spacing: .8px; color: var(--steel-grey);
  }

  .address { position: absolute; left: 22px; top: 218px; font-size: 12.5px; line-height: 17px; font-style: normal; }
  .address .web { color: var(--brand-blue); }

  .contacts { position: absolute; right: 21px; top: 201px; list-style: none; font-size: 12.5px; line-height: 17.3px; text-align: right; }
  .contacts li { display: flex; align-items: center; justify-content: flex-end; gap: 6px; }
  .contacts svg { width: 11px; height: 11px; fill: var(--brand-blue); flex: none; }
</style>
</head>
<body>
<main class="canvas">

  <section class="card card--back" aria-label="Card back">
    <div class="wordmark">Vantrell Forge Works</div>
    <div class="tagline">BUILT FOR WHAT'S NEXT</div>
    <div class="site"><span class="rule"></span><span>www.vantrellforge.com</span><span class="rule"></span></div>
  </section>

  <section class="card card--front" aria-label="Card front">
    <div class="header-band"></div>

    <div class="holder">
      <div class="name">Marcus Ellery Dane</div>
      <div class="role">Managing Director</div>
    </div>

    <div class="wordmark">Vantrell Forge Works</div>
    <div class="tagline">BUILT FOR WHAT'S NEXT</div>

    <address class="address">
      1870 Tolliver Ave., Brookhaven,<br>
      OH 45219, USA<br>
      <span class="web">www.vantrellforge.com</span>
    </address>

    <ul class="contacts">
      <li>513-555-0142 (ext. 214)
        <svg viewBox="0 0 12 12"><path d="M1 4 C1 2 3 1 6 1 S11 2 11 4 V5 H8 V4 H4 V5 H1 Z M3 6 H9 L10 11 H2 Z"/></svg></li>
      <li>513-555-0187
        <svg viewBox="0 0 12 12"><path d="M3 0 H9 V12 H3 Z"/><rect x="4" y="1.5" width="4" height="7" fill="#fff"/></svg></li>
      <li>513-555-0143
        <svg viewBox="0 0 12 12"><path d="M3 0 H9 V4 H3 Z M1 4 H11 V9 H9 V12 H3 V9 H1 Z"/><rect x="4" y="8" width="4" height="3" fill="#fff"/></svg></li>
      <li>mdane@vantrellforge.com
        <svg viewBox="0 0 12 12"><path d="M0 2 H12 V10 H0 Z"/><path d="M0.5 2.5 L6 7 L11.5 2.5" stroke="#fff" stroke-width="1" fill="none"/></svg></li>
    </ul>
  </section>

</main>
</body>
</html>
```